Fine Art business needs new website

We need a simple website with a home page, about us page, New sculptures, Sold sculptures, and a contact us page.Our sculptures are very high end one of a kind pieces. As such we need the site to be VERY elegant and professional. Lastly, because I'll be updating pictures on the website on a monthly basis it needs to be user friendly to update (Wordpress is preferred). The only branding we have so far for the business is a business card.
Updates
I wasn't completely ready when this project launched, also I am on the road right now and haven't been able to be as responsive to all you designers as I would like. I will work on giving feedback to all the top designs we've received so far. Thank you all so much for your participation and hardwork.
Target Market(s)
High end customers (affluent), art collectors, interior decorators/designers
Industry/Entity Type
Art Gallery
Coding
Coded - Design and coding required
Number of Pages Required
5+ page
Requirements
Must have
- Easily editable picture gallery for myself so that I can add new pieces(pictures of the pieces), remove sold pieces, etc. I would like the website to be built in wordpress so I can update it. I currently use mangewordpress through Netmarro for my other business website and would like to do the same for this one.
- Pages:
- -Intro page with featured pieces
- -Current pieces gallery (for sale) mainly a picture gallery
- -Sculptures archive (sold pieces) another picture gallery
- -About us: Pull-down of -about the artist (attached content)
- -Artistic Process (attached content)
- -Show Schedule:
- -one page dedicated to "friends of TMV" (basically a link page)
- TO BE CLEAR "www.pineroverslane.com" IS A TOTALLY DIFFERENT SITE AND I'M NOT TRYING TO COMBINE THE TWO OR JOIN THEM INTO ONE. This page needs be more elegant and seperate from the Pine Rovers site.
- UPDATE: I'd like a link to the TMV Faceplume page: https://www.faceplume-social.com/mirelcraftworks/
Nice to have
- I would like the pictures on the gallery pages able to have text connected with them (Materials, price)
- I would like the site style and fonts to be similar to our business cards we've already had designed (picture attached).
Should not have
- Too much flash or other things that will make the site slow to load.

```html
<!DOCTYPE html>
<html lang="en">
<head>
<meta charset="utf-8">
<title>Stone Art Gallery</title>
<link href="https://fonts.googleapis.com/css2?family=Lato:wght@400;700&display=swap" rel="stylesheet">
<style>
:root{
  --page:#f3f3f3;
  --hero-dark:#1c1b20;
  --hero-mid:#3a3940;
  --white:#ffffff;
  --ink:#2b2b2b;
  --accent:#6c63b3;
  --card:#1a1a1a;
  --footer:#262626;
  --social-blue:#3d8fd1;
  --social-red:#c8232c;
  --social-navy:#3b5998;
  --social-slate:#4f7fa8;
}
*{margin:0;padding:0;box-sizing:border-box}
html,body{width:1200px;height:2439px;overflow:hidden}
body{position:relative;background:var(--page);font-family:'Lato',sans-serif;color:var(--ink)}

.hero{position:absolute;left:0;top:0;width:1200px;height:298px;
  background:
    radial-gradient(ellipse 55% 70% at 68% 35%,rgba(110,108,118,.55) 0%,rgba(60,58,66,.25) 45%,transparent 75%),
    linear-gradient(180deg,#2c2b31 0%,var(--hero-mid) 45%,var(--hero-dark) 100%);
  box-shadow:0 3px 8px rgba(0,0,0,.35)}
.nav{position:absolute;top:29px;left:0;font-size:14px;font-weight:700;color:var(--white);letter-spacing:.2px}
.nav a{position:absolute;color:var(--white);text-decoration:none;white-space:nowrap}
.nav .about::after{content:"";position:absolute;right:-14px;top:6px;border:3px solid transparent;border-top-color:#aaa}
.nav .current{border-bottom:2px solid var(--accent);padding-bottom:6px}
.menu-toggle{position:absolute;left:976px;top:28px;width:36px}
.menu-toggle span{display:block;height:3px;background:var(--white);margin-bottom:5px}
.hero-title{position:absolute;top:91px;left:0;width:1200px;text-align:center;color:var(--white);font-size:27px;font-weight:700;letter-spacing:.5px}
.hero-rule{position:absolute;top:134px;left:546px;width:110px;height:1px;background:#bbb}
.hero-intro{position:absolute;top:161px;left:150px;width:900px;text-align:center;color:#e4e4e4;font-size:17.5px;line-height:26px}

.sorting{position:absolute;left:858px;top:340px;width:153px;height:42px;border:1.5px solid #333;background:var(--page);font-size:13px;font-weight:700;display:flex;align-items:center;padding-left:17px;color:#333}
.sorting svg{margin-left:8px}
.sort-menu{position:absolute;left:844px;top:402px;width:167px;height:71px;background:var(--white);box-shadow:0 2px 6px rgba(0,0,0,.25);font-size:13px;color:#333;z-index:2}
.sort-menu li{list-style:none;position:absolute;left:22px}

.card{position:absolute;width:248px}
.card .photo{width:248px;height:342px;border-radius:6px;box-shadow:2px 4px 6px rgba(0,0,0,.35);position:relative;overflow:hidden;
  background:
    radial-gradient(ellipse 30% 40% at 50% 42%,var(--tone) 0%,var(--tone-soft) 45%,transparent 100%),
    radial-gradient(ellipse 55% 14% at 50% 92%,#3a2621 0%,transparent 100%),
    linear-gradient(180deg,#1e1e1e 0%,var(--card) 60%,#141414 100%)}
.card .name{text-align:center;font-size:17px;margin-top:13px;color:#2d2d2d}
.card .price{text-align:center;font-size:14px;color:var(--accent);margin-top:4px}
.hover-layer{position:absolute;inset:0;background:rgba(90,90,90,.55);display:flex;align-items:center;justify-content:center}

.pager{position:absolute;top:2172px;left:528px;display:flex;align-items:center;font-size:16px;color:#555}
.pager span{display:flex;align-items:center;justify-content:center;width:33px;height:31px;border:1.5px solid #666;border-radius:3px}
.pager .gap{border:none;width:34px;font-size:22px;font-weight:700;padding-bottom:2px}
.pager .spacer{width:11px;border:none}

.footer{position:absolute;left:0;top:2229px;width:1200px;height:210px;background:var(--footer);color:var(--white)}
.footer h2{position:absolute;top:40px;font-size:22px;font-weight:700}
.footer p,.footer li{font-size:12.5px;line-height:21.5px;color:#eee}
.about-text{position:absolute;left:198px;top:72px;width:230px}
.address{position:absolute;left:527px;top:72px;list-style:none}
.address li{display:flex;align-items:center}
.address svg{margin-right:8px;width:14px}
.address .contact{font-weight:700;padding-left:22px}
.social{position:absolute;left:866px;top:80px;width:160px;display:grid;grid-template-columns:80px 80px;row-gap:6px;list-style:none}
.social li{display:flex;align-items:center;font-size:12px;line-height:16px;color:#eee}
.social li::before{content:"";width:11px;height:11px;border-radius:2px;margin-right:6px;background:var(--mark)}
</style>
</head>
<body>
<header class="hero">
  <nav class="nav">
    <a style="left:194px">HOME</a>
    <a class="about" style="left:257px">ABOUT</a>
    <a class="current" style="left:343px">GALLERY</a>
    <a style="left:424px">CONTACT</a>
  </nav>
  <div class="menu-toggle"><span></span><span></span><span></span></div>
  <h1 class="hero-title">STONE ART GALLERY</h1>
  <div class="hero-rule"></div>
  <p class="hero-intro">Lorem ipsum dolor sit amet, consectetur adipiscing elit. Donec vulputate ac velit et sagittis.<br>Phasellus fermentum lacinia eros, at blandit tellus vestibulum sit amet. Fusce ultricies felis lorem,<br>et ullamcorper urna feugiat ac.</p>
</header>

<div class="sorting">Default Sorting
  <svg width="14" height="8" viewBox="0 0 14 8"><path d="M1 1l6 6 6-6" fill="none" stroke="#333" stroke-width="1.5"/></svg>
</div>
<ul class="sort-menu">
  <li style="top:18px">* NEW (10)</li>
  <li style="top:46px">Archived (45)</li>
</ul>

<main class="gallery">
  <div class="card" style="left:189px;top:434px"><div class="photo" role="img" aria-label="Green malachite sculpture on a wooden pedestal" style="--tone:#2a6e4e;--tone-soft:rgba(30,80,58,.45)"></div><p class="name">Sculpture Name</p><p class="price">$179</p></div>
  <div class="card" style="left:476px;top:434px"><div class="photo" role="img" aria-label="Brown agate slice sculpture on a pedestal" style="--tone:#7a5535;--tone-soft:rgba(95,65,40,.45)"></div><p class="name">Sculpture Name</p><p class="price">$179</p></div>
  <div class="card" style="left:763px;top:434px"><div class="photo" role="img" aria-label="Blue geode stacked sculpture on a black base" style="--tone:#4a60a0;--tone-soft:rgba(60,75,125,.45)"></div><p class="name">Sculpture Name</p><p class="price">$179</p></div>

  <div class="card" style="left:189px;top:863px"><div class="photo" role="img" aria-label="Purple amethyst geode on a gold stand" style="--tone:#5b4590;--tone-soft:rgba(75,58,120,.45)"></div><p class="name">Sculpture Name</p><p class="price">$179</p></div>
  <div class="card" style="left:476px;top:863px"><div class="photo" role="img" aria-label="Amber backlit stone sculpture" style="--tone:#b07a30;--tone-soft:rgba(150,100,40,.45)"></div><p class="name">Sculpture Name</p><p class="price">$179</p></div>
  <div class="card" style="left:763px;top:863px"><div class="photo" role="img" aria-label="Tall green jade sculpture" style="--tone:#4b6a5a;--tone-soft:rgba(62,88,74,.45)">
    <div class="hover-layer"><svg width="64" height="64" viewBox="0 0 64 64"><circle cx="26" cy="26" r="17" fill="none" stroke="#fff" stroke-width="5"/><path d="M38 38l18 18" stroke="#fff" stroke-width="8" stroke-linecap="round"/></svg></div>
  </div><p class="name">Sculpture Name</p><p class="price">$179</p></div>

  <div class="card" style="left:189px;top:1293px"><div class="photo" role="img" aria-label="Golden swirling wood and stone sculpture" style="--tone:#8f6128;--tone-soft:rgba(120,82,38,.45)"></div><p class="name">Sculpture Name</p><p class="price">$179</p></div>
  <div class="card" style="left:476px;top:1293px"><div class="photo" role="img" aria-label="Brown crystal cluster over purple geode" style="--tone:#6a4a3a;--tone-soft:rgba(88,62,50,.45)"></div><p class="name">Sculpture Name</p><p class="price">$179</p></div>
  <div class="card" style="left:763px;top:1293px"><div class="photo" role="img" aria-label="Cream coral fossil stacked sculpture" style="--tone:#a8966e;--tone-soft:rgba(135,120,90,.45)"></div><p class="name">Sculpture Name</p><p class="price">$179</p></div>

  <div class="card" style="left:189px;top:1722px"><div class="photo" role="img" aria-label="Amethyst geode on a wooden pedestal" style="--tone:#5d4585;--tone-soft:rgba(78,58,112,.45)"></div><p class="name">Sculpture Name</p><p class="price">$179</p></div>
  <div class="card" style="left:476px;top:1722px"><div class="photo" role="img" aria-label="Orange crystal geode on a black base" style="--tone:#a05a26;--tone-soft:rgba(135,78,34,.45)"></div><p class="name">Sculpture Name</p><p class="price">$179</p></div>
  <div class="card" style="left:763px;top:1722px"><div class="photo" role="img" aria-label="Blue lace agate slice sculpture" style="--tone:#6a7e98;--tone-soft:rgba(88,105,128,.45)"></div><p class="name">Sculpture Name</p><p class="price">$179</p></div>
</main>

<nav class="pager"><span>1</span><span class="spacer"></span><span>2</span><span class="gap">...</span><span>10</span></nav>

<footer class="footer">
  <h2 style="left:198px">ABOUT US</h2>
  <p class="about-text">This is a dummy text just<br>to provide text in the About Us<br>section which will be added correctly<br>later on.</p>
  <h2 style="left:527px">OUR ADDRESS</h2>
  <ul class="address">
    <li><svg viewBox="0 0 14 14" height="14"><path d="M3 1l3 3-2 2c1 2 2 3 4 4l2-2 3 3-2 2C6 13 1 8 1 3z" fill="#fff"/></svg>(555) 214-0398</li>
    <li><svg viewBox="0 0 14 10" height="10"><rect x=".5" y=".5" width="13" height="9" fill="none" stroke="#fff"/><path d="M.5.5L7 6l6.5-5.5" fill="none" stroke="#fff"/></svg>mara@pinerovers-mail.com</li>
    <li><svg viewBox="0 0 14 14" height="14"><path d="M6 8l2-2M5 6L3 8a2 2 0 003 3l2-2M9 8l2-2a2 2 0 00-3-3L6 5" fill="none" stroke="#fff" stroke-width="1.3"/></svg>www.mirelstoneworks.com</li>
    <li class="contact">CONTACT US</li>
  </ul>
  <h2 style="left:854px">KEEP IN TOUCH</h2>
  <ul class="social">
    <li style="--mark:var(--social-blue)">Chirply</li>
    <li style="--mark:var(--social-red)">Pinora</li>
    <li style="--mark:var(--social-navy)">Faceplume</li>
    <li style="--mark:var(--social-slate)">Snapgrid</li>
  </ul>
</footer>
</body>
</html>
```